Business Card Design Project

Basic business card with minimal details. I just need company name, email & web address, telephone and my name.
I would like the back of the card to be grey with my logo & company name centred.

Target Market(s)

Architects
Builders
Property Developers

Industry/Entity Type

Business

Font styles to use
Sans Serif

Colors

Designer to choose colors to be used in the design.

Requirements
Must have
• Tallow Crest
Rupert Hazelby - Director
M: 0427 915203
E: rupert@tallowcrest.com.au
W: www.tallowcrest.com.au
Should not have
• No other images or pictures

```html
<!DOCTYPE html>
<html lang="en">
<head>
<meta charset="utf-8">
<title>Tallow Crest – Business Card</title>
<link href="https://fonts.googleapis.com/css2?family=Arimo:wght@400;700&display=swap" rel="stylesheet">
<style>
  :root {
    --backdrop: #e4e4e3;
    --card-light: #bdbdbc;
    --card-dark: #80807e;
    --band-white: #ffffff;
    --accent-red: #c8312e;
    --ink-grey: #7b7b7b;
    --ink-soft: #8d8d8d;
    --ink-white: #ffffff;
  }
  * { margin: 0; padding: 0; box-sizing: border-box; }
  html, body {
    width: 1200px; height: 999px; overflow: hidden;
    background: var(--backdrop);
    font-family: "Arimo", Arial, sans-serif;
  }
  .stage { position: relative; width: 1200px; height: 999px; }

  .card-back {
    position: absolute; left: 233px; top: 43px; width: 746px; height: 425px;
    background: linear-gradient(120deg, var(--card-light) 0%, #a3a3a2 40%, var(--card-dark) 75%);
  }
  .brand {
    position: absolute; left: 110px; top: 182px;
    display: flex; align-items: center; gap: 26px;
  }
  .brand-square { width: 52px; height: 52px; background: var(--accent-red); }
  .brand-name {
    color: var(--ink-white); font-weight: 400; font-size: 54px;
    letter-spacing: 3px; line-height: 1; text-transform: uppercase;
  }

  .card-front {
    position: absolute; left: 233px; top: 518px; width: 746px; height: 430px;
    background: var(--band-white);
  }
  .identity { position: absolute; left: 32px; top: 44px; }
  .person-name {
    color: var(--ink-grey); font-weight: 700; font-size: 31px; line-height: 1;
    text-transform: uppercase;
  }
  .person-role { color: var(--ink-soft); font-size: 23px; margin-top: 6px; }

  .contact-band {
    position: absolute; left: 0; top: 152px; width: 746px; height: 278px;
    background: linear-gradient(110deg, var(--card-dark) 0%, #999998 55%, #b3b3b2 100%);
  }
  .contact-list { list-style: none; position: absolute; left: 32px; top: 34px; }
  .contact-item {
    display: flex; align-items: center; gap: 22px; height: 34px; margin-bottom: 41px;
    color: var(--ink-white); font-size: 24px;
  }
  .contact-icon { width: 32px; height: 32px; flex: none; }
</style>
</head>
<body>
<main class="stage">
  <section class="card-back" aria-label="Card back">
    <div class="brand">
      <span class="brand-square"></span>
      <span class="brand-name">Tallow Crest</span>
    </div>
  </section>

  <section class="card-front" aria-label="Card front">
    <div class="identity">
      <p class="person-name">Rupert Hazelby</p>
      <p class="person-role">Director</p>
    </div>
    <div class="contact-band">
      <ul class="contact-list">
        <li class="contact-item">
          <svg class="contact-icon" viewBox="0 0 32 32" fill="none" stroke="var(--accent-red)" stroke-width="1.5">
            <rect x="9" y="2" width="14" height="28" rx="2"/>
            <line x1="9" y1="6" x2="23" y2="6"/>
            <line x1="9" y1="24" x2="23" y2="24"/>
            <circle cx="16" cy="27" r="1.3"/>
          </svg>
          <span>0427 915203</span>
        </li>
        <li class="contact-item">
          <svg class="contact-icon" viewBox="0 0 32 32" fill="none" stroke="var(--accent-red)" stroke-width="1.5">
            <rect x="1" y="8" width="30" height="17"/>
            <polyline points="1,8 16,19 31,8"/>
            <line x1="1" y1="25" x2="12" y2="16"/>
            <line x1="31" y1="25" x2="20" y2="16"/>
          </svg>
          <span>rupert@tallowcrest.com.au</span>
        </li>
        <li class="contact-item">
          <svg class="contact-icon" viewBox="0 0 32 32" fill="none" stroke="var(--accent-red)" stroke-width="1.3">
            <polyline points="0,10 3,17 6,10 9,17 12,10 15,17 18,10 21,17 24,10"/>
            <polygon points="22,14 22,30 26,26 30,31 31,29 27,24 32,23"/>
          </svg>
          <span>www.tallowcrest.com.au</span>
        </li>
      </ul>
    </div>
  </section>
</main>
</body>
</html>
```